Business card design for holistic health care clinic

We need a double-sided business card design for our holistic health care clinic that integrates our logo design and also its color scheme. My business is called Valmira. It is an integrative medicine clinic. You have already done the logo for me. Please ensure an elegant and upscale design that is not cluttered, but still has all the necessary information (please see below for details).

Target Market(s)

Wellness, fitness, rehabilitation for educated, well-traveled open-minded clients who are focused on natural, organic, balanced and preventive healthcare and lifestyle.

Industry/Entity Type

Medical

Contact Information for Business Card

Modern, clean.

Number of Pages Required

1 page

Font styles to use
Serif
Sans Serif

Colors

Designer to choose colors to be used in the design.

Requirements
Must have
• Logo on one side, all other information on the other side.
• Other information should include:
• Tobias Wrenfeld - DOE, CPT, LMT
• 4100 East Marrow Drive
• Austin, TX 78119
• 512 555 0148
• 818 555 0192
• info@ValmiraHealth.example
• t.wrenfeld@ValmiraHealth.example
Nice to have
• Darker background on front - but not totally black - shaded/dark gray.

```html
<!DOCTYPE html>
<html lang="en">
<head>
<meta charset="utf-8">
<title>Valmira – Business Card</title>
<link rel="stylesheet" href="https://fonts.googleapis.com/css2?family=Nunito:wght@700;800&family=Roboto:ital,wght@0,400;0,500;1,400&family=Roboto+Condensed:wght@700&display=swap">
<style>
  :root {
    --backdrop: #d6ab80;
    --card-light: #f3f3f3;
    --card-dark: #252728;
    --brand-blue: #0b8fcd;
    --stripe-dark: #2b2d2f;
    --text-light: #ffffff;
    --rule: #8a8c8e;
  }
  html, body {
    margin: 0;
    padding: 0;
    width: 1200px;
    height: 960px;
    overflow: hidden;
    background: var(--backdrop);
  }
  .canvas {
    position: relative;
    width: 1200px;
    height: 960px;
  }
  .card {
    position: absolute;
    width: 600px;
    height: 342px;
    overflow: hidden;
    box-shadow: 2px 3px 5px rgba(0,0,0,0.35);
  }
  .card--info { left: 314px; top: 113px; background: var(--card-light); }
  .card--brand { left: 311px; top: 472px; background: var(--card-dark); }

  .card__tab {
    position: absolute;
    left: 0; top: 44px;
    width: 9px; height: 41px;
    background: var(--brand-blue);
    border-radius: 0 6px 6px 0;
  }
  .holder {
    position: absolute;
    left: 32px; top: 53px;
    margin: 0;
    font-family: "Roboto Condensed", sans-serif;
    font-weight: 700;
    font-size: 21px;
    color: var(--brand-blue);
    text-transform: uppercase;
    letter-spacing: 0.2px;
  }
  .holder__credentials { font-size: 12px; }

  .brand {
    position: absolute;
    text-align: center;
    color: var(--brand-blue);
    font-family: "Nunito", sans-serif;
  }
  .brand__name {
    display: block;
    font-weight: 800;
    line-height: 1;
    letter-spacing: 1px;
    text-transform: uppercase;
  }
  .brand__descriptor {
    display: block;
    font-weight: 700;
  }
  .card--info .brand { left: 322px; top: 88px; width: 250px; }
  .card--info .brand__name { font-size: 50px; }
  .card--info .brand__descriptor { font-size: 14.5px; margin-top: 4px; }
  .card--brand .brand { left: 150px; top: 130px; width: 300px; }
  .card--brand .brand__name { font-size: 66px; }
  .card--brand .brand__descriptor { font-size: 18px; margin-top: 6px; }

  .wave { position: absolute; left: 0; top: 0; }

  .contact {
    position: absolute;
    left: 34px; top: 218px;
    margin: 0;
    padding: 0;
    list-style: none;
    font-family: "Roboto", sans-serif;
    font-size: 14.5px;
    line-height: 19px;
    color: var(--text-light);
  }
  .contact__label { font-weight: 500; }
  .contact__address { margin-top: 6px; }

  .tagline {
    position: absolute;
    left: 0; right: 0; top: 284px;
    display: flex;
    align-items: center;
    justify-content: center;
    gap: 6px;
    margin: 0;
    font-family: "Roboto", sans-serif;
    font-style: italic;
    font-size: 16.5px;
    color: var(--text-light);
  }
  .tagline::before, .tagline::after {
    content: "";
    width: 110px;
    height: 1px;
  }
  .tagline::before { background: linear-gradient(to right, transparent, var(--rule)); }
  .tagline::after { background: linear-gradient(to left, transparent, var(--rule)); }
</style>
</head>
<body>
<main class="canvas">
  <section class="card card--info" aria-label="Card back: contact details">
    <div class="card__tab"></div>
    <h1 class="holder">Tobias Wrenfeld <span class="holder__credentials">- DOE, CPT, LMT</span></h1>
    <div class="brand">
      <span class="brand__name">Valmira</span>
      <span class="brand__descriptor">Integrative Holistic Medicine</span>
    </div>
    <svg class="wave" width="600" height="342" viewBox="0 0 600 342" aria-hidden="true">
      <path d="M0,192 C110,170 220,182 320,240 C420,300 520,336 600,342 L0,342 Z" fill="var(--brand-blue)"/>
      <g fill="none" stroke="var(--stripe-dark)">
        <path d="M0,188 C110,166 222,178 322,236 C422,296 522,334 600,341" stroke-width="4"/>
        <path d="M60,181 C150,170 240,186 330,240 C430,300 520,334 600,340" stroke-width="1.5"/>
        <path d="M90,182 C170,174 250,192 340,246 C435,304 525,336 600,341" stroke-width="1.5"/>
        <path d="M120,184 C190,180 260,198 350,252 C440,308 530,338 600,342" stroke-width="1.5"/>
      </g>
    </svg>
    <ul class="contact">
      <li><span class="contact__label">P:</span> 512 555 0148</li>
      <li><span class="contact__label">C:</span> 818 555 0192</li>
      <li><span class="contact__label">E:</span> t.wrenfeld@ValmiraHealth.example</li>
      <li><span class="contact__label">W:</span> www.ValmiraHealth.example</li>
      <li class="contact__address">4100 East Marrow Drive , Austin, TX 78119</li>
    </ul>
  </section>

  <section class="card card--brand" aria-label="Card front: brand">
    <div class="brand">
      <span class="brand__name">Valmira</span>
      <span class="brand__descriptor">Integrative Holistic Medicine</span>
    </div>
    <p class="tagline">helping the body help itself</p>
  </section>
</main>
</body>
</html>
```